BrivoTerna. Lantern of the Steady Harvest. Business card

Professional business card for BrivoTerna (Lantern of the Steady Harvest)
My rationale: Strategy-> Execution-> Results-> Value that lead to the BrivoTerna name: We put the Lantern of the Steady Harvest.
We deliver value to our customers helping them at defining a good strategy (cyan arrow). 90% of well formulated strategies fail due to poor execution so we also consider strategical execution very important (green arrow). Due to the execution we obtain the results (blue arrow). Finally, the results provide feedback to redefine strategy, and the new strategy has to be executed and new results obtained providing new feedback and on and on. It's like a wheel that finally, must create corporate value: value for shareholders, staholders, employees, providers...-

Target Market(s)

CEOs and steering comitees , invewrnent funds

Industry/Entity Type

Business Consultant

Contact Information for Business Card

Teodoro Vinsquel
CEO & Founder
teodoro.vinsquel@brivoterna-example.com
Mobile: +34 655.803.912
www.brivoterna-example.com

Colors

Designer to choose colors to be used in the design.

Requirements
Nice to have
• Nice to hace the words: Strategy, execution, results
• Nice to vave the claim: Lantern of the Steady Harvest
• The three colors should be shown:
• cyan for STRATEGY
• green for EXECUTION
• blue for RESULTS
Should not have
• Complete black background

```html
<!DOCTYPE html>
<html lang="en">
<head>
<meta charset="utf-8">
<title>BrivoTerna — Business Card</title>
<link rel="stylesheet" href="https://fonts.googleapis.com/css2?family=Ubuntu:wght@700&family=Open+Sans:wght@400;600&display=swap">
<style>
  :root {
    --backdrop: #e8e6e3;
    --card-white: #ffffff;
    --brand-navy: #1a3a9a;
    --brand-green: #8cc63f;
    --brand-cyan: #29abe2;
    --text-grey: #3a3a3a;
    --back-light: #1e9be0;
    --back-deep: #0a3fa6;
    --url-light: #e6f2ff;
  }
  * { margin: 0; padding: 0; box-sizing: border-box; }
  html, body {
    width: 1200px;
    height: 997px;
    overflow: hidden;
    background: var(--backdrop);
  }
  .sheet {
    position: relative;
    width: 1200px;
    height: 997px;
  }
  .card {
    position: absolute;
    top: 344px;
    width: 540px;
    height: 309px;
    overflow: hidden;
    box-shadow: 0 10px 28px rgba(0,0,0,0.14), 0 2px 5px rgba(0,0,0,0.08);
  }

  /* Front side */
  .card--front {
    left: 40px;
    background: var(--card-white);
  }
  .front__wordmark {
    position: absolute;
    top: 38px;
    right: 44px;
    font-family: "Ubuntu", sans-serif;
    font-weight: 700;
    font-size: 40px;
    letter-spacing: -1px;
    color: var(--brand-navy);
  }
  .front__tab {
    position: absolute;
    top: 100px;
    right: 0;
    width: 16px;
    height: 26px;
    background: var(--brand-green);
  }
  .front__details {
    position: absolute;
    top: 104px;
    right: 44px;
    text-align: right;
    font-family: "Open Sans", sans-serif;
    color: var(--text-grey);
  }
  .details__name {
    font-family: "Ubuntu", sans-serif;
    font-weight: 700;
    font-size: 17px;
    color: var(--brand-navy);
  }
  .details__role {
    font-size: 12px;
    margin-bottom: 8px;
  }
  .details__line {
    display: flex;
    justify-content: flex-end;
    align-items: center;
    gap: 6px;
    font-size: 12px;
    line-height: 17px;
  }
  .details__icon {
    width: 12px;
    height: 12px;
    flex: none;
  }
  .details__spacer { width: 12px; flex: none; }

  /* Back side */
  .card--back {
    left: 620px;
    background: radial-gradient(ellipse at 50% 40%, var(--back-light) 0%, #1577d2 45%, var(--back-deep) 100%);
  }
  .back__wordmark {
    position: absolute;
    top: 112px;
    left: 0;
    width: 100%;
    text-align: center;
    font-family: "Ubuntu", sans-serif;
    font-weight: 700;
    font-size: 48px;
    letter-spacing: -1px;
    color: var(--brand-navy);
  }
  .back__url {
    position: absolute;
    top: 220px;
    left: 0;
    width: 100%;
    text-align: center;
    font-family: "Open Sans", sans-serif;
    font-size: 14px;
    letter-spacing: 4px;
    color: var(--url-light);
  }
</style>
</head>
<body>
  <main class="sheet">
    <section class="card card--front" aria-label="Business card front">
      <div class="front__wordmark">BrivoTerna</div>
      <div class="front__tab"></div>
      <div class="front__details">
        <p class="details__name">Teodoro Vinsquel</p>
        <p class="details__role">CEO &amp; Founder</p>
        <p class="details__line">
          <span>+34 655.803.912</span>
          <svg class="details__icon" viewBox="0 0 12 12" aria-hidden="true">
            <circle cx="6" cy="6" r="5.5" fill="none" stroke="#1a3a9a" stroke-width="1"/>
            <path d="M4 3.2 L5 3 L5.5 4.6 L4.8 5.1 Q5.4 6.6 6.9 7.2 L7.4 6.5 L9 7 L8.8 8 Q6.5 8.6 4.7 6.8 Q3.2 5.2 4 3.2Z" fill="#1a3a9a"/>
          </svg>
        </p>
        <p class="details__line">
          <span>teodoro.vinsquel@brivoterna-example.com</span>
          <svg class="details__icon" viewBox="0 0 12 12" aria-hidden="true">
            <rect x="1" y="2.5" width="10" height="7" fill="#1a3a9a"/>
            <path d="M1 2.5 L6 6.5 L11 2.5" fill="none" stroke="#ffffff" stroke-width="0.9"/>
          </svg>
        </p>
        <p class="details__line">
          <span>www.brivoterna-example.com</span>
          <svg class="details__icon" viewBox="0 0 12 12" aria-hidden="true">
            <circle cx="6" cy="6" r="5" fill="none" stroke="#1a3a9a" stroke-width="1"/>
            <ellipse cx="6" cy="6" rx="2.2" ry="5" fill="none" stroke="#1a3a9a" stroke-width="0.8"/>
            <line x1="1" y1="6" x2="11" y2="6" stroke="#1a3a9a" stroke-width="0.8"/>
          </svg>
        </p>
      </div>
    </section>

    <section class="card card--back" aria-label="Business card back">
      <div class="back__wordmark">BrivoTerna</div>
      <div class="back__url">www.brivoterna-example.com</div>
    </section>
  </main>
</body>
</html>
```